Your Kid is fantastic Postcards

Tarvell State School
Attached is the one that I did up front and back – this is a postcard for the principal to send to parents about something wonderful their child had done at the school.
We want the mural photo on the front (see attached) with the window blocked out with the words from the principal put there instead. The Postcard will probably have to be long due to the photo as I tried to make one in zoomley and it left half the postcard blank we would ideally have like the A6 size. On the back will need to be as per the back of my sample one. Our website is www.tarvellss.qzedu.example cheers and thanks
School

```html
<!DOCTYPE html>
<html lang="en">
<head>
<meta charset="utf-8">
<title>Tarvell State School – Principal Postcard</title>
<link rel="stylesheet" href="https://fonts.googleapis.com/css2?family=Montserrat:wght@400;500;600&family=Alex+Brush&display=swap">
<style>
  :root {
    --page-bg: #ececec;
    --sky-deep: #2f63b0;
    --sky-light: #5d9be0;
    --strip-blue: #6fb4ea;
    --grass-deep: #1f8a3a;
    --grass-light: #5cc24a;
    --lime-edge: #9bd83e;
    --mural-warm: #e99a3a;
    --mural-green: #4f9a45;
    --mural-blue: #4a86c8;
    --ink: #2b2b2b;
    --script-blue: #2448a8;
    --label-green: #3aa04a;
    --card-white: #ffffff;
  }
  * { box-sizing: border-box; margin: 0; padding: 0; }
  html, body { width: 1200px; height: 794px; overflow: hidden; }
  body {
    background: var(--page-bg);
    font-family: "Montserrat", sans-serif;
    color: var(--ink);
    position: relative;
  }
  .postcard {
    position: absolute;
    top: 199px;
    width: 560px;
    height: 396px;
    background: var(--card-white);
    box-shadow: 0 6px 18px rgba(0,0,0,0.18);
    overflow: hidden;
  }
  .postcard--back { left: 30px; }
  .postcard--front { left: 610px; }
  .postcard svg { position: absolute; inset: 0; }

  /* back side */
  .school-name {
    position: absolute;
    top: 44px; left: 250px;
    font-size: 13px; font-weight: 600;
    color: var(--sky-deep);
    white-space: nowrap;
    display: flex; align-items: center; gap: 8px;
  }
  .school-name .dot {
    width: 12px; height: 12px; border-radius: 50%;
    background: var(--sky-deep);
    flex: none;
  }
  .postage-area {
    position: absolute;
    top: 22px; right: 22px;
    width: 78px; height: 64px;
    border: 1.5px solid var(--ink);
    display: flex; align-items: center; justify-content: center;
    text-align: center;
    font-size: 11px; font-weight: 600; line-height: 1.25;
  }
  .address-lines {
    position: absolute;
    top: 150px; right: 30px;
    width: 210px;
  }
  .address-lines span {
    display: block;
    border-bottom: 1px solid var(--ink);
    height: 38px;
  }
  .message {
    position: absolute;
    top: 210px; left: 34px;
    width: 228px;
    font-size: 14px; line-height: 1.6;
  }
  .message .dear {
    display: flex; gap: 6px;
  }
  .message .dear i {
    flex: 1;
    border-bottom: 1.5px dotted var(--ink);
    margin-bottom: 6px;
  }
  .sign-off {
    position: absolute;
    bottom: 28px; left: 34px;
    font-size: 14px; line-height: 1.5;
  }

  /* front side */
  .principal-box {
    position: absolute;
    left: 78px; top: 214px;
    width: 300px; height: 100px;
    background: var(--card-white);
    border: 1px solid #c9d6e6;
    padding: 10px 18px;
    display: flex; align-items: flex-end; gap: 10px;
    white-space: nowrap;
  }
  .principal-box .from {
    font-size: 15px; color: var(--label-green);
    margin-bottom: 20px;
  }
  .principal-box .title {
    font-family: "Alex Brush", cursive;
    font-size: 50px; line-height: 1;
    color: var(--script-blue);
    margin-bottom: 10px;
  }
</style>
</head>
<body>

  <section class="postcard postcard--back" aria-label="Postcard back">
    <svg width="560" height="396" viewBox="0 0 560 396">
      <defs>
        <linearGradient id="backMuralFade" x1="0" y1="1" x2="1" y2="0">
          <stop offset="0" stop-color="#4f9a45"/>
          <stop offset="0.5" stop-color="#8cc4a0" stop-opacity="0.7"/>
          <stop offset="1" stop-color="#ffffff" stop-opacity="0"/>
        </linearGradient>
      </defs>
      <path role="img" aria-label="Faded strip of the school mural artwork"
            d="M0 210 L0 120 L230 40 L250 40 L250 60 L0 260 Z"
            fill="url(#backMuralFade)"/>
      <line x1="280" y1="80" x2="280" y2="360" stroke="#555" stroke-width="1" stroke-dasharray="2 4"/>
    </svg>
    <div class="school-name"><span class="dot"></span>Tarvell State School</div>
    <div class="postage-area">Postage<br>Area</div>
    <div class="address-lines"><span></span><span></span><span></span></div>
    <div class="message">
      <p class="dear">Dear <i></i></p>
      <p>This postcard is to let you know how proud I am that</p>
    </div>
    <p class="sign-off">Yours sincerely,<br>Ms Principal</p>
  </section>

  <section class="postcard postcard--front" aria-label="Postcard front">
    <svg width="560" height="396" viewBox="0 0 560 396">
      <defs>
        <linearGradient id="sky" x1="0" y1="0" x2="1" y2="1">
          <stop offset="0" stop-color="#5d9be0"/>
          <stop offset="1" stop-color="#2f63b0"/>
        </linearGradient>
        <linearGradient id="grass" x1="0" y1="0" x2="1" y2="1">
          <stop offset="0" stop-color="#5cc24a"/>
          <stop offset="1" stop-color="#1f8a3a"/>
        </linearGradient>
        <linearGradient id="mural" x1="0" y1="1" x2="1" y2="0">
          <stop offset="0" stop-color="#4f9a45"/>
          <stop offset="0.35" stop-color="#e99a3a"/>
          <stop offset="0.7" stop-color="#4f9a45"/>
          <stop offset="1" stop-color="#4a86c8"/>
        </linearGradient>
      </defs>
      <rect width="560" height="396" fill="url(#sky)"/>
      <rect x="0" y="170" width="560" height="28" fill="#6fb4ea" opacity="0.7"/>
      <path role="img" aria-label="Colourful school mural with cartoon dragons, a butterfly and graffiti lettering"
            d="M0 190 C150 130 330 60 560 30 L560 190 C400 220 220 290 60 396 L0 396 Z"
            fill="url(#mural)"/>
      <path d="M60 396 C220 290 400 220 560 190 L560 206 C410 232 240 300 90 396 Z"
            fill="#9bd83e"/>
      <path d="M90 396 C240 300 410 232 560 206 L560 396 Z" fill="url(#grass)"/>
      <path d="M0 190 C150 130 330 60 560 30" fill="none" stroke="#ffffff" stroke-width="4"/>
    </svg>
    <div class="principal-box">
      <span class="from">From The</span>
      <span class="title">Principal</span>
    </div>
  </section>

</body>
</html>
```